uk based ecommerce website requires fresh look ,high quality look and feel

we are a web based company selling eco friendly ground reinforcement grids to diy and construction sectors
our existing website is www.pondermeshpaths.co.uk ,

we have already updated the logo so that is the branding sorted .so we need a ecommerce website that is very much up-to date in design and layout and which has content management system for ease of use so that we can add products and information as required.

Use current logo as reference for colour scheme.
www.pondermeshpaths.co.uk

The current website has 6 pages accessible through the navigation bar, I would now like 5 pages, removing the need for the Trade Enquiries page possibly have it with along with contact us.

Target Market(s)

construction industry , diy end users,
retail market, landscapers, gardeners

Industry/Entity Type

Construction

Font styles to use
Other font styles liked:
• logo font prometo

Colors
f78f20
9bcb3c

Requirements
Must have
• logo colours and logo design in website with cms responsive design for tablet and mobile devices
• expect content to work flawlessly and look great across all devices
• HTML 5 custom design with coding as required
• must have good experiance in ecommerce website design
• eye catching, high quality look and feel and very user friedly ,very up-to date.
Nice to have
• picture slider show
• explain in writing what exactly i am getting in my ecommerce website
Should not have
• plain , basic design , old fashion looking ,cheap look

```html
<!DOCTYPE html>
<html lang="en">
<head>
<meta charset="utf-8">
<title>PonderMesh Ground Solutions</title>
<link href="https://fonts.googleapis.com/css2?family=Open+Sans:wght@400;600;700;800&display=swap" rel="stylesheet">
<style>
:root{
  --orange:#f78f20;
  --orange-dark:#e07a10;
  --green:#9bcb3c;
  --green-dark:#7fae25;
  --ink:#3d3d3d;
  --muted:#8a8a8a;
  --line:#e3e3e3;
  --paper:#ffffff;
  --soft:#f4f4f4;
  --night:#2f2f2f;
  --stone:#9a9a9a;
}
*{box-sizing:border-box;margin:0;padding:0}
html,body{width:1200px;height:2360px;overflow:hidden}
body{font-family:"Open Sans",Arial,sans-serif;color:var(--ink);background:var(--paper);font-size:13px;position:relative}
.wrap{width:860px;margin:0 auto;position:relative}

/* header */
.site-header{height:152px;background:linear-gradient(#fafafa,#fff)}
.site-header .wrap{height:152px}
.brand{position:absolute;left:0;top:26px;display:flex;align-items:center;gap:12px}
.brand-mark{width:62px;height:62px;border-radius:50%;background:var(--green)}
.brand-name{font-weight:800;font-size:27px;color:var(--green-dark);line-height:1;letter-spacing:.5px}
.brand-name small{display:block;font-size:12px;letter-spacing:2px;margin-top:5px}
.account-links{position:absolute;left:300px;top:12px;font-size:10px;color:var(--muted);text-transform:uppercase}
.account-links span{margin:0 6px}
.account-links .on{color:var(--green-dark);font-weight:700}
.cart-btn{position:absolute;right:0;top:8px;background:var(--orange);color:#fff;font-size:11px;font-weight:700;padding:5px 14px;border-radius:3px}
.contact-block{position:absolute;right:0;top:52px;text-align:left;width:190px}
.contact-block .tel{display:flex;align-items:center;gap:8px;font-size:20px;font-weight:700;color:var(--orange);line-height:1.2}
.contact-block .tel.green{color:var(--green-dark)}
.contact-block .ico{width:18px;height:18px}
.contact-block .note{font-size:11px;color:var(--muted);font-weight:600;margin-left:26px}

/* nav */
.main-nav{height:40px;background:var(--green)}
.main-nav .wrap{display:flex;align-items:center;height:40px}
.main-nav a{color:#fff;text-decoration:none;font-size:12px;font-weight:700;text-transform:uppercase;padding:0 16px;height:40px;line-height:40px}
.main-nav a.active{background:var(--orange)}
.search{margin-left:auto;width:170px;height:24px;background:#fff;border-radius:3px;font-size:11px;color:var(--muted);padding:4px 8px;display:flex;justify-content:space-between}

/* hero */
.hero{height:400px;background:linear-gradient(90deg,var(--orange),#fba54a 50%,var(--orange))}
.hero .wrap{padding-top:28px}
.slide{height:340px;background:linear-gradient(160deg,#b9b9b9,#6f6f6f 60%,#4c4c4c);border:4px solid #fff;box-shadow:0 3px 10px rgba(0,0,0,.3);position:relative}
.slide-caption{position:absolute;left:18px;bottom:22px;color:#fff;font-weight:700;font-size:14px;background:rgba(0,0,0,.35);padding:4px 10px}
.slide-arrow{position:absolute;top:150px;width:28px;height:38px;background:rgba(0,0,0,.4);color:#fff;text-align:center;line-height:38px;font-size:18px}
.slide-arrow.prev{left:0}.slide-arrow.next{right:0}
.dots{display:flex;gap:6px;justify-content:center;margin-top:6px}
.dots i{width:8px;height:8px;border-radius:50%;background:#fff;opacity:.6}
.dots i.on{opacity:1;background:var(--green)}

/* welcome */
.welcome{text-align:center;padding:20px 40px 0;height:150px}
.welcome h1{font-size:21px;font-weight:700;color:var(--ink);text-transform:uppercase}
.welcome h1 em{font-style:normal;color:var(--green-dark)}
.welcome .rule{width:60px;height:3px;background:var(--orange);margin:8px auto 12px}
.welcome p{font-size:12px;color:var(--muted);line-height:1.7}

.section-title{font-size:14px;font-weight:700;border-bottom:2px solid var(--line);padding-bottom:6px;position:relative}
.section-title::after{content:"";position:absolute;left:0;bottom:-2px;width:110px;height:2px;background:var(--orange)}
.section-title small{font-size:10px;color:var(--muted);font-weight:400;margin-left:14px}

.grid{display:grid;grid-template-columns:repeat(4,1fr);gap:20px;margin-top:22px}
.product{text-align:center}
.hex{width:160px;height:180px;margin:0 auto;clip-path:polygon(50% 0,100% 25%,100% 75%,50% 100%,0 75%,0 25%);background:var(--orange);position:relative}
.hex .photo{position:absolute;inset:7px;clip-path:polygon(50% 0,100% 25%,100% 75%,50% 100%,0 75%,0 25%)}
.p-grey .photo{background:linear-gradient(135deg,#cfcfcf,#7d7d7d)}
.p-dark .photo{background:linear-gradient(135deg,#5a5a5a,#242424)}
.p-stone .photo{background:linear-gradient(135deg,#b7ab98,#6e6558)}
.p-turf .photo{background:linear-gradient(135deg,#8fc04a,#3f7a22)}
.p-green .photo{background:linear-gradient(135deg,#a8d85a,#5d9a2a)}
.price-tag{position:absolute;left:50%;top:50%;transform:translate(-50%,-50%);background:rgba(0,0,0,.55);color:#fff;padding:6px 12px;font-size:13px;font-weight:700;line-height:1.3}
.price-tag small{display:block;font-size:10px;font-weight:400}
.product h3{font-size:10px;font-weight:700;text-transform:uppercase;color:var(--ink);margin-top:10px;line-height:1.4;height:30px}
.buy{display:flex;justify-content:center;gap:6px;margin-top:8px}
.buy span{font-size:11px;font-weight:700;color:#fff;padding:6px 10px;border-radius:2px}
.buy .shop{background:var(--green)}
.buy .cost{background:var(--orange)}

.featured{height:260px}
.category{padding-top:12px}
.category .grid{row-gap:52px}
.load-more{text-align:center;margin-top:78px;font-size:13px;font-weight:600;color:var(--muted)}

/* perks */
.perks{display:flex;justify-content:space-between;padding:0 40px;margin-top:38px;height:90px}
.perk{display:flex;align-items:center;gap:12px;font-size:13px;font-weight:700;line-height:1.3}
.perk svg{width:54px;height:60px}

/* newsletter */
.newsletter{height:70px;background:var(--night);margin-top:16px}
.newsletter .wrap{display:flex;align-items:center;height:70px}
.newsletter h2{color:#fff;font-size:17px;font-weight:700;text-transform:uppercase}
.newsletter p{color:#aaa;font-size:10px;margin-top:2px}
.newsletter .field{margin-left:auto;display:flex}
.newsletter .field span{width:160px;height:28px;background:#fff;font-size:10px;color:var(--muted);padding:7px 8px}
.newsletter .field b{width:34px;height:28px;background:var(--orange);color:#fff;text-align:center;line-height:28px}

/* footer */
.site-footer{height:226px;background:var(--soft)}
.site-footer .wrap{display:grid;grid-template-columns:1fr 1fr 1.2fr 1.2fr;gap:20px;padding-top:24px}
.site-footer h4{font-size:12px;font-weight:700;text-transform:uppercase;margin-bottom:10px;color:var(--ink)}
.site-footer li{list-style:none;font-size:10px;color:var(--muted);line-height:1.9}
.site-footer li::before{content:"›";color:var(--orange);margin-right:6px}
.contact-list li::before{content:none}
.social{display:grid;grid-template-columns:1fr 1fr;gap:8px 10px}
.social span{display:flex;align-items:center;gap:6px;font-size:10px;color:var(--muted)}
.social i{width:22px;height:22px;border-radius:50%;background:var(--green)}
.cards{display:flex;gap:5px;margin-top:14px}
.cards i{width:30px;height:19px;background:#d6d6d6;border-radius:2px}
.base-bar{position:absolute;left:0;bottom:0;width:1200px;height:34px;background:var(--orange);color:#fff;text-align:center;font-size:10px;line-height:34px}
</style>
</head>
<body>

<header class="site-header">
  <div class="wrap">
    <div class="brand">
      <div class="brand-mark"></div>
      <div class="brand-name">PONDERMESH<small>GROUND SOLUTIONS</small></div>
    </div>
    <div class="account-links"><span>Login</span>|<span>Register</span>|<span class="on">My Account</span>|<span>Checkout</span></div>
    <div class="cart-btn">0 ITEMS £0.00 ▾</div>
    <div class="contact-block">
      <div class="tel">
        <svg class="ico" viewBox="0 0 24 24"><path fill="#f78f20" d="M6.6 10.8a15 15 0 006.6 6.6l2.2-2.2c.3-.3.7-.4 1-.2 1.1.4 2.3.6 3.6.6.6 0 1 .4 1 1V20c0 .6-.4 1-1 1A17 17 0 013 4c0-.6.4-1 1-1h3.5c.6 0 1 .4 1 1 0 1.3.2 2.5.6 3.6.1.3 0 .7-.2 1z"/></svg>
        0123-456-7890</div>
      <div class="tel green">
        <svg class="ico" viewBox="0 0 24 24"><path fill="#7fae25" d="M6.6 10.8a15 15 0 006.6 6.6l2.2-2.2c.3-.3.7-.4 1-.2 1.1.4 2.3.6 3.6.6.6 0 1 .4 1 1V20c0 .6-.4 1-1 1A17 17 0 013 4c0-.6.4-1 1-1h3.5c.6 0 1 .4 1 1 0 1.3.2 2.5.6 3.6.1.3 0 .7-.2 1z"/></svg>
        0800-555-0147</div>
      <div class="note">24 HOUR MESSAGING SERVICE</div>
    </div>
  </div>
</header>

<nav class="main-nav">
  <div class="wrap">
    <a>Shop</a><a class="active">About Us</a><a>Ground Solutions</a><a>PonderMesh</a><a>Contact Us</a>
    <div class="search"><span>Search...</span><span>⌕</span></div>
  </div>
</nav>

<section class="hero">
  <div class="wrap">
    <div class="slide" role="img" aria-label="Photo of grey honeycomb ground grid filled with gravel">
      <span class="slide-arrow prev">‹</span><span class="slide-arrow next">›</span>
      <div class="slide-caption">PONDERMESH SYSTEM</div>
    </div>
    <div class="dots"><i class="on"></i><i></i><i></i><i></i></div>
  </div>
</section>

<section class="welcome wrap">
  <h1>Welcome to <em>PonderMesh Ground Solutions</em></h1>
  <div class="rule"></div>
  <p>Eco friendly ground reinforcement grids for driveways, paths, lawns and car parks. Our strong recycled cells hold gravel and turf firmly in place, stop rutting and allow water to drain naturally. Ideal for DIY projects, landscapers, gardeners and the construction trade, with fast UK delivery and friendly expert advice on every order.</p>
</section>

<section class="featured wrap">
  <h2 class="section-title">Featured Products</h2>
  <div class="grid">
    <div class="product"><div class="hex p-grey"><div class="photo" role="img" aria-label="Photo of a grey gravel grid sheet"></div></div><h3>Gravel Grid Drive Sheet</h3></div>
    <div class="product"><div class="hex p-dark"><div class="photo" role="img" aria-label="Photo of black turf mesh"></div><div class="price-tag">£ 123.00<small>View Details</small></div></div><h3>Turfgrass Reinforcement<br>Mesh</h3></div>
    <div class="product"><div class="hex p-stone"><div class="photo" role="img" aria-label="Photo of honeycomb grid with gravel"></div></div><h3>PonderMesh Honeycomb System</h3></div>
    <div class="product"><div class="hex p-green"><div class="photo" role="img" aria-label="Photo of green turf reinforcement mesh"></div></div><h3>Turfgrass Reinforcement<br>Mesh</h3></div>
  </div>
</section>

<section class="category wrap">
  <h2 class="section-title">Shop by Category <small>Ground Solution Products</small></h2>
  <div class="grid">
    <div class="product"><div class="hex p-green"><div class="photo" role="img" aria-label="Photo of green ground grid"></div></div><h3>PonderMesh Grids<br>(Green)</h3><div class="buy"><span class="shop">SHOP NOW</span><span class="cost">£ 30.00</span></div></div>
    <div class="product"><div class="hex p-dark"><div class="photo" role="img" aria-label="Photo of black mesh roll"></div><div class="price-tag">£ 30.00<small>View Details</small></div></div><h3>Turfgrass Reinforcement<br>Mesh</h3><div class="buy"><span class="shop">SHOP NOW</span><span class="cost">£ 30.00</span></div></div>
    <div class="product"><div class="hex p-stone"><div class="photo" role="img" aria-label="Photo of gravel filled grid"></div></div><h3>PonderMesh Honeycomb System</h3><div class="buy"><span class="shop">SHOP NOW</span><span class="cost">£ 30.00</span></div></div>
    <div class="product"><div class="hex p-turf"><div class="photo" role="img" aria-label="Photo of grass growing through mesh"></div></div><h3>Turfgrass Reinforcement<br>Mesh</h3><div class="buy"><span class="shop">SHOP NOW</span><span class="cost">£ 30.00</span></div></div>

    <div class="product"><div class="hex p-grey"><div class="photo" role="img" aria-label="Photo of grey ground grid"></div></div><h3>PonderMesh Grids<br>(Grey)</h3><div class="buy"><span class="shop">SHOP NOW</span><span class="cost">£ 30.00</span></div></div>
    <div class="product"><div class="hex p-stone"><div class="photo" role="img" aria-label="Photo of decorative gravel"></div></div><h3>Turfgrass Reinforcement<br>Mesh</h3><div class="buy"><span class="shop">SHOP NOW</span><span class="cost">£ 30.00</span></div></div>
    <div class="product"><div class="hex p-dark"><div class="photo" role="img" aria-label="Photo of black honeycomb grid"></div></div><h3>PonderMesh Honeycomb System</h3><div class="buy"><span class="shop">SHOP NOW</span><span class="cost">£ 30.00</span></div></div>
    <div class="product"><div class="hex p-turf"><div class="photo" role="img" aria-label="Photo of reinforced lawn"></div></div><h3>Turfgrass Reinforcement<br>Mesh</h3><div class="buy"><span class="shop">SHOP NOW</span><span class="cost">£ 30.00</span></div></div>
  </div>
  <div class="load-more">Load More...</div>
</section>

<section class="perks wrap">
  <div class="perk">
    <svg viewBox="0 0 54 60"><polygon points="27,2 52,16 52,44 27,58 2,44 2,16" fill="none" stroke="#9a9a9a" stroke-width="3"/><path d="M14 24h16v12H14zM30 28h6l4 4v4H30z" fill="#9a9a9a"/><circle cx="19" cy="38" r="3" fill="#9a9a9a"/><circle cx="35" cy="38" r="3" fill="#9a9a9a"/></svg>
    <span>FREE Standard<br>Delivery</span></div>
  <div class="perk">
    <svg viewBox="0 0 54 60"><polygon points="27,2 52,16 52,44 27,58 2,44 2,16" fill="none" stroke="#9a9a9a" stroke-width="3"/><path d="M17 30l7 7 13-14" fill="none" stroke="#9a9a9a" stroke-width="4"/></svg>
    <span>100%<br>Satisfaction</span></div>
  <div class="perk">
    <svg viewBox="0 0 54 60"><polygon points="27,2 52,16 52,44 27,58 2,44 2,16" fill="none" stroke="#9a9a9a" stroke-width="3"/><path d="M16 22h20l4 8-4 8H16z" fill="#9a9a9a"/></svg>
    <span>Great Deals |<br>Shop Now</span></div>
</section>

<section class="newsletter">
  <div class="wrap">
    <div><h2>Subscribe for our newsletter</h2><p>Sign up today for offers, new products and ground reinforcement tips.</p></div>
    <div class="field"><span>Enter your email</span><b>›</b></div>
  </div>
</section>

<footer class="site-footer">
  <div class="wrap">
    <div><h4>Quick Links</h4><ul><li>Shop</li><li>About Us</li><li>Ground Solutions</li><li>Category</li><li>Customer Service</li><li>Delivery Area</li><li>Contact Us</li></ul></div>
    <div><h4>Our Policies</h4><ul><li>Site Account</li><li>Payment Methods</li><li>Refunds and Returns</li><li>Returns &amp; Exchange</li><li>Secure Shopping</li><li>Terms &amp; Conditions</li><li>Privacy Policy</li></ul></div>
    <div><h4>Contact Info</h4><ul class="contact-list"><li>Meadow House, Unit 4 Green Hill Road,<br>Ashford, Kent TN23 9QX</li><li>hello@pondermeshpaths.co.uk</li><li>0123-456-7890 | 0800-555-0147</li><li>24 Hour Messaging Service</li></ul></div>
    <div><h4>Follow Us</h4>
      <div class="social"><span><i></i>Friends</span><span><i></i>Updates</span><span><i></i>Pinboard</span><span><i></i>Circles</span></div>
      <div class="cards"><i></i><i></i><i></i><i></i><i></i></div>
    </div>
  </div>
</footer>

<div class="base-bar">© 2024 www.pondermeshpaths.co.uk | All rights reserved.</div>

</body>
</html>
```